IT Company needs Website for new Web and Mobile products for Sports and Fitness

Background:

We developed web based white label frontend web solution, backend services and white label mobile apps for to log, analyze, share and control sport and fitness activities. The name of this product suite is "Trevantix" (http://trevantix-example.com)

This products will be used by customers that provide platforms and community systems for sport and fitness. One of the major USP's is, that our technology i open for nearly all common formats, devices and apps out in the market. This means, you can just upload your data directly from device, file or app - e.G. Kestrel, Bolvane, Ravelo, StrideVault, Pacelumo, Zembra and much others.

Two current concrete examples/References

(1) MyQuorel
It's an international platform from quorel for runners. It provides individual training lans and a training log. MyQuorel uses the Backend Product "Trevantix Hub" (see http://hub.trevantix-example.net for a landing page) to integrate device, file and app support. Before this, every user has to track his training with manual inputs

(2) Paceharbor and fen-zine
Both are German customers. Paceharor is focused on runners. fen-zine is focused on Triatheletes. Both use the Product "Trevantix Web". This is a complete web solution with web based frontend solutions for athletes and coaches.

What do we need?
We need website layout for B2B for our products. We don't need lot's of pages. We need the pretty and nice layout, so we can derive the pages we need.

IMPORTANT
We don't talk about the webpages for the product itself (this will be a different project in future). We talk about a website, explaining the products)
Updates

Hi all,

we just start reviewing the first designs, and try to give feedback as detailed as possible. We attached a PDF document, to describe the the products a little bit more detailed. 

As written in the description, in the end we have two different sections. One is the usual stuff like "start page", "about", "contact", "disclaimer", "pricing", "blah...." and one will be the Developer Section, the "Tec Section". This ist aimed to developers (of our customers) that will integrate our products in there existing system or which will integrate our services in there own software.  This "pages" are more like "documentation", so easy to read and cool to look at (cause developers likes it cool, but straight)

Dear all,

we just do the final review. Cause this week is with heavy load, it takes some time...

Cheers

Odell

Target Market(s)

* Platforms and Communities for sport, health and fitness
* Gyms

Industry/Entity Type

Concrete

Font styles to use
Sans Serif

Requirements
Must have
• * Templates shall base on bootstrap. If not, it shall be easily realized on our site with bootstrap or out of the box "full responsive"

* HTML5 / CSS3
Nice to have
• PAGES
- Start Page
- Generic Template (from which we can derive additional pages)
- Contact Page
- Disclaimer Page
- Blog/News Page
- "About us" Page (can be combined with disclaimer)
- One Example product page (in end we have 3 products), shall show (if you need product details, let me know)
- product and it's description
- pricing information
- Add-Ons for the product
- Developer Section Page (Start Point for developers, where the finde "basic technical concepts and developer API's
- Example Developer Page for technical concept
- Example Developer Page for API

LOGO ISSUE
You can use an align to the Logo attached OR provide a new logo. The given logo is a logo for our own B2C Website http://trevantix-example.net. It's not really necessary, that the logo or the color must be used for the product website. Maybe it will be better if it's a complete new one, to avoid irritation between Trevantix as a B2B product and trevantix-example.net as a B2C platform.
Should not have
• No Flash and other proprietary technologies

```html
<!DOCTYPE html>
<html lang="en">
<head>
<meta charset="utf-8">
<title>Trevantix – Backend Services</title>
<link href="https://fonts.googleapis.com/css2?family=Open+Sans:wght@400;600;700&display=swap" rel="stylesheet">
<style>
  :root {
    --brand-blue: #1f6fd8;
    --nav-blue: #2a74c9;
    --text-dark: #333333;
    --text-body: #3d3d3d;
    --rule: #d6d6d6;
    --menu-border: #ececec;
    --white: #ffffff;
    --button-grey: #555555;
  }
  * { box-sizing: border-box; margin: 0; padding: 0; }
  html, body { width: 1200px; height: 516px; overflow: hidden; }
  body { font-family: "Open Sans", Arial, sans-serif; color: var(--text-dark); background: var(--white); position: relative; }

  .site-header {
    position: absolute; left: 0; top: 0; width: 1200px; height: 68px;
    background: var(--white); box-shadow: 0 1px 4px rgba(0,0,0,0.12); z-index: 5;
  }
  .brand {
    position: absolute; left: 36px; top: 10px;
    display: flex; align-items: center; gap: 8px;
    font-size: 26px; font-weight: 600; color: var(--brand-blue); letter-spacing: 0.5px;
  }
  .brand-mark { width: 20px; height: 20px; background: var(--brand-blue); }
  .main-nav { position: absolute; top: 21px; left: 600px; display: flex; }
  .main-nav a {
    font-size: 13px; font-weight: 600; color: var(--text-dark);
    text-decoration: none; text-transform: uppercase; margin-right: 33px;
  }
  .main-nav a.is-active { color: var(--nav-blue); }

  .hero {
    position: absolute; left: 0; top: 68px; width: 1200px; height: 448px;
    background:
      radial-gradient(circle at 440px 150px, rgba(226,214,180,0.55) 0, rgba(226,214,180,0) 70px),
      radial-gradient(circle at 270px 420px, rgba(190,180,160,0.5) 0, rgba(190,180,160,0) 90px),
      linear-gradient(90deg, #eeeeee 0%, #f3f3f3 50%, #e9e9e9 100%);
  }
  .hero-kicker {
    position: absolute; left: 44px; top: 76px; white-space: nowrap;
    font-size: 22px; font-weight: 400; color: var(--text-dark);
  }
  .hero-title {
    position: absolute; left: 44px; top: 112px;
    font-size: 52px; font-weight: 700; color: var(--brand-blue); letter-spacing: 0.5px;
  }
  .hero-rule { position: absolute; left: 44px; width: 520px; height: 1px; background: var(--rule); }
  .hero-rule.top { top: 190px; }
  .hero-rule.bottom { top: 306px; }
  .hero-text {
    position: absolute; left: 44px; top: 212px; width: 520px;
    font-size: 15.5px; line-height: 24px; color: var(--text-body);
  }
  .btn {
    position: absolute; display: flex; align-items: center; justify-content: center; gap: 10px;
    font-size: 16px; text-transform: uppercase; border-radius: 2px; background: transparent;
  }
  .btn-primary { left: 44px; top: 336px; width: 175px; height: 45px; border: 1px solid var(--nav-blue); color: var(--nav-blue); }
  .btn-secondary { left: 237px; top: 339px; width: 158px; height: 44px; border: 1px solid var(--button-grey); color: var(--button-grey); }
  .btn svg { width: 15px; height: 15px; }

  .hero-portrait {
    position: absolute; left: 620px; top: 27px; width: 450px; height: 421px;
    border-radius: 160px 160px 0 0;
    background: linear-gradient(180deg, #4a3a34 0%, #c9a58f 30%, #e8e4e4 52%, #2c3550 68%, #222a40 100%);
  }

  .dropdown {
    position: absolute; left: 654px; top: 60px; width: 172px; z-index: 6;
    background: var(--white); box-shadow: 0 2px 6px rgba(0,0,0,0.15); list-style: none;
  }
  .dropdown li {
    height: 37.2px; line-height: 37px; padding-left: 15px;
    font-size: 11px; text-transform: uppercase; color: var(--text-dark);
    border-bottom: 1px solid var(--menu-border);
  }
  .dropdown li:last-child { border-bottom: none; }
</style>
</head>
<body>
  <header class="site-header">
    <div class="brand"><span class="brand-mark"></span>Trevantix</div>
    <nav class="main-nav">
      <a class="is-active" href="#">Home</a>
      <a class="is-active" href="#">Pages</a>
      <a href="#">Features</a>
      <a href="#">Portfolio</a>
      <a href="#">Blog</a>
      <a href="#">Contact</a>
    </nav>
  </header>

  <ul class="dropdown">
    <li>About Page Style 1</li>
    <li>About Page Style 2</li>
    <li>Services Style 1</li>
    <li>Services Style 2</li>
    <li>Full Width Page</li>
    <li>Left Sidebar Page</li>
    <li>Right Sidebar Page</li>
    <li>Left Navigation</li>
    <li>Right Navigation</li>
    <li>404 Error Page</li>
  </ul>

  <section class="hero" role="img" aria-label="Soft blurred office background">
    <p class="hero-kicker">We Developed Web Based Frontend Web Solution,Mobile Apps</p>
    <h1 class="hero-title">BACKEND SERVICES</h1>
    <div class="hero-rule top"></div>
    <p class="hero-text">Many desktop publishing packages and web page editors now use the lorem Ipsum as their default model text, and a search for 'lorem ipsum will uncover many web sites still in their infancy.</p>
    <div class="hero-rule bottom"></div>
    <a class="btn btn-primary" href="#">
      <svg viewBox="0 0 16 16"><path d="M15 1 1 7l6 2 2 6z" fill="currentColor"/></svg>Get Started
    </a>
    <a class="btn btn-secondary" href="#">
      <svg viewBox="0 0 16 16"><path d="M1 7h3v8H1zM5 7l3-6c1.5 0 2 1 1.7 2.5L9.3 6H14c1 0 1.6.9 1.3 1.8l-1.8 6.3c-.2.6-.7.9-1.3.9H5z" fill="none" stroke="currentColor" stroke-width="1.2"/></svg>Buy Now!
    </a>
    <div class="hero-portrait" role="img" aria-label="Photo of a smiling businesswoman in a dark pinstripe suit with hands folded"></div>
  </section>
</body>
</html>
```